Visual design for database driven web application

Need a clean, professional looking visual design for a web application.

BRIMM is the new standardized K-12 school testing program for the state of Texas. We are building an application named BRIMM-Lookout (clever, yeah?) that will allow teachers, school administrators, and others to EASILY sort through millions of records of student data and print or export reports showing just the information they need about their students.

The state currently doesn't provide a user-friendly way to do this. They provide a "data dump" spreadsheet that school administrators and teachers must figure out how to manipulate to get the data they need. We are building a Web-based tool that will make it super simple and easy for our users to get the data they need in a format that works for them.

I've created a basic wireframe of the main application screen in Vellido QX Plus. I need you to "skin" the wireframe to make it look good. Your mockup will set the tone for branding and visual design throughout the site.

See the attached screenshots. There are a few variations of the screen that include dynamic panels that open & close. Start by designing just the main screen and if you have time, do one or two of the panels. Thanks!
Updates

Target Market(s)

K-12 education professionals (teachers, administrators) in the state of Texas

Industry/Entity Type

Building

Requirements
Must have
• Your mockups should include all of the features & content shown in the attached screenshots.

However, you don't have to show all 10 rows of data. You can just do the column headers and one row of data. (It would be repetitive and unnecessary to spend time re-creating the entire grid with all of that data just to show your visual styling.)

The design should reflect the following concepts:

- Texas
- Education
- Simplicity
- Helpfulness
- Trust
- Professionalism

If I select your design, I will want your design source files (Illustrator, Photoshop, etc.)
Nice to have
• A logo in the upper left corner for BRIMM-Lookout. The logo should definitely communicate the design concepts described under "must have."

```html
<!DOCTYPE html>
<html lang="en">
<head>
<meta charset="utf-8">
<title>BRIMM-Lookout — Student Data</title>
<link rel="stylesheet" href="https://fonts.googleapis.com/css2?family=Marcellus&family=Noto+Sans:wght@400;700&display=swap">
<style>
:root{
  --bg-top:#1ea5ba;
  --bg-bottom:#2cb9cf;
  --rule:#a9dde6;
  --ink:#1d2b30;
  --link:#cfeff4;
  --tab-active:#14c4ec;
  --tab-idle:#2a98ab;
  --panel:#1c8e9e;
  --head-row:#b9dee4;
  --cell:#1e9bb5;
  --row-top:#ffffff;
  --row-bottom:#eaf7f9;
  --row-line:#1c8e9e;
  --footer:#a6e1e9;
  --btn:#e2f4f6;
  --btn-ink:#3f6f78;
  --show:#1b9ab3;
  --spin:#c3e8ee;
  --field:#4cbfd0;
  --field-border:#137d8d;
}
*{box-sizing:border-box;margin:0;padding:0}
html,body{width:1200px;height:803px;overflow:hidden}
body{
  position:relative;
  font-family:"Noto Sans",Verdana,sans-serif;
  background:linear-gradient(180deg,var(--bg-top) 0,var(--bg-top) 150px,var(--bg-bottom) 803px);
  color:var(--ink);
}
.brand{
  position:absolute;left:70px;top:58px;
  font-family:"Marcellus",Georgia,serif;
  font-size:41px;color:#eef8fa;letter-spacing:1px;
}
.welcome{position:absolute;left:594px;top:32px;font-size:15px}
.account{position:absolute;left:810px;top:32px;font-size:13px;font-weight:700;color:var(--link);letter-spacing:1px}
.account span{margin:0 6px}
.tools{position:absolute;left:1061px;top:22px;display:flex;gap:18px}
.search-field{
  position:absolute;left:811px;top:73px;width:253px;height:32px;
  background:var(--field);border:2px solid var(--field-border);
}
.search-field svg{position:absolute;right:2px;top:1px}
.search-btn{
  position:absolute;left:1075px;top:76px;width:92px;height:19px;
  background:var(--tab-active);border-radius:3px;
  color:#fff;font-size:14px;font-weight:700;text-align:center;line-height:19px;
}
.search-option{position:absolute;left:923px;top:106px;font-size:13px;color:var(--link);display:flex;gap:6px;align-items:center}
.divider{position:absolute;left:0;top:142px;width:1200px;height:7px;background:var(--rule)}
.tab{
  position:absolute;top:195px;width:205px;height:35px;
  font-size:17px;color:#e8f9fc;text-align:center;line-height:35px;
}
.tab.active{left:105px;background:var(--tab-active)}
.tab.idle{left:334px;width:204px;background:var(--tab-idle)}
.panel{position:absolute;left:37px;top:230px;width:1131px;height:452px;background:var(--panel)}
.grid{position:absolute;left:13px;top:23px;width:1104px}
.row{
  display:grid;
  grid-template-columns:67px 67px 61px 118px 86px 121px 109px 120px 42px 124px 70px 119px;
}
.row.head{height:33px;background:var(--head-row);font-size:15px}
.row.head div{border-right:2px solid #fff;display:flex;align-items:center;justify-content:center}
.row.head div:last-child{border-right:0}
.row.data{
  height:34.6px;margin-top:1.2px;
  background:linear-gradient(180deg,var(--row-top),var(--row-bottom));
  color:var(--cell);font-size:15px;
}
.row.head + .row.data{margin-top:8px}
.row.data div{display:flex;align-items:center;justify-content:center}
.row.data.hover{font-weight:700}
.pager{
  position:absolute;left:37px;top:694px;width:1130px;height:48px;
  background:var(--footer);border-radius:3px;
}
.pages{position:absolute;left:44px;top:14px;font-size:15px}
.pages b{font-weight:400;margin-left:16px}
.pages i{font-style:normal;color:#7ebcc6}
.btn{
  position:absolute;top:14px;width:109px;height:26px;background:var(--btn);
  color:var(--btn-ink);font-size:15px;font-weight:700;text-align:center;line-height:26px;
}
.btn.next{left:269px}
.btn.prev{left:393px}
.show{position:absolute;left:883px;top:14px;font-size:16px;font-weight:700;color:var(--show)}
.spinner{
  position:absolute;left:945px;top:9px;width:84px;height:32px;background:var(--spin);border-radius:4px;
  font-size:15px;font-weight:700;color:var(--btn-ink);
}
.spinner span{position:absolute;left:18px;top:6px}
.spinner svg{position:absolute;right:8px;top:4px}
</style>
</head>
<body>
  <header>
    <div class="brand">BRIMM-Lookout</div>
    <div class="welcome">Welcome &nbsp;: Jack</div>
    <div class="account">My Profile <span>/</span>Logout</div>
    <div class="tools">
      <svg width="22" height="22" viewBox="0 0 22 22" aria-label="Print">
        <rect x="6" y="2" width="10" height="6" fill="#fff"/>
        <rect x="2" y="8" width="18" height="8" rx="2" fill="#d9e6e9"/>
        <rect x="6" y="13" width="10" height="7" fill="#fff" stroke="#7aa" stroke-width="1"/>
        <circle cx="17" cy="11" r="1.2" fill="#3c3"/>
      </svg>
      <svg width="20" height="22" viewBox="0 0 20 22" aria-label="Export">
        <rect x="2" y="2" width="16" height="18" rx="1" fill="#2b3b44"/>
        <rect x="5" y="3" width="10" height="6" fill="#fff"/>
        <rect x="5" y="13" width="10" height="6" fill="#9fb2b8"/>
        <path d="M13 10 l5 5 -5 5z" fill="#f2c230"/>
      </svg>
    </div>
    <div class="search-field">
      <svg width="36" height="28" viewBox="0 0 36 28" aria-hidden="true">
        <circle cx="15" cy="12" r="8" fill="none" stroke="#16525c" stroke-width="3"/>
        <line x1="21" y1="18" x2="30" y2="26" stroke="#16525c" stroke-width="4" stroke-linecap="round"/>
      </svg>
    </div>
    <div class="search-btn">Search</div>
    <div class="search-option">Search &nbsp;Option
      <svg width="24" height="14" viewBox="0 0 24 14" aria-hidden="true"><path d="M1 1 H23 L12 13Z" fill="none" stroke="#cfeff4" stroke-width="1.5"/></svg>
    </div>
  </header>
  <div class="divider"></div>

  <div class="tab active">Instructions</div>
  <div class="tab idle">Sutent Data</div>

  <main class="panel">
    <div class="grid">
      <div class="row head"><div>Date</div><div>Grade</div><div>ESC</div><div>CDC#</div><div>District</div><div>Campus</div><div>Last Name</div><div>First Name</div><div>MI</div><div>Student ID</div><div>Gender</div><div>DOB</div></div>
      <div class="row data"><div>411</div><div>9</div><div>10</div><div>9999999999</div><div>Example</div><div>Examble H S</div><div>Alvorado</div><div>NATHALE</div><div>I</div><div>1234546734</div><div>F</div><div>28/03/1980</div></div>
      <div class="row data"><div>411</div><div>9</div><div>10</div><div>9999999999</div><div>Example</div><div>Examble H S</div><div>Alvorado</div><div>NATHALE</div><div>I</div><div>1234546734</div><div>F</div><div>28/03/1980</div></div>
      <div class="row data"><div>411</div><div>9</div><div>10</div><div>9999999999</div><div>Example</div><div>Examble H S</div><div>Alvorado</div><div>NATHALE</div><div>I</div><div>1234546734</div><div>F</div><div>28/03/1980</div></div>
      <div class="row data"><div>411</div><div>9</div><div>10</div><div>9999999999</div><div>Example</div><div>Examble H S</div><div>Alvorado</div><div>NATHALE</div><div>I</div><div>1234546734</div><div>F</div><div>28/03/1980</div></div>
      <div class="row data"><div>411</div><div>9</div><div>10</div><div>9999999999</div><div>Example</div><div>Examble H S</div><div>Alvorado</div><div>NATHALE</div><div>I</div><div>1234546734</div><div>F</div><div>28/03/1980</div></div>
      <div class="row data hover"><div>411</div><div>9</div><div>10</div><div>9999999999</div><div>Example</div><div>Examble H S</div><div>Alvorado</div><div>NATHALE</div><div>I</div><div>1234546734</div><div>F</div><div>28/03/1980</div></div>
      <div class="row data"><div>411</div><div>9</div><div>10</div><div>9999999999</div><div>Example</div><div>Examble H S</div><div>Alvorado</div><div>NATHALE</div><div>I</div><div>1234546734</div><div>F</div><div>28/03/1980</div></div>
      <div class="row data"><div>411</div><div>9</div><div>10</div><div>9999999999</div><div>Example</div><div>Examble H S</div><div>Alvorado</div><div>NATHALE</div><div>I</div><div>1234546734</div><div>F</div><div>28/03/1980</div></div>
      <div class="row data"><div>411</div><div>9</div><div>10</div><div>9999999999</div><div>Example</div><div>Examble H S</div><div>Alvorado</div><div>NATHALE</div><div>I</div><div>1234546734</div><div>F</div><div>28/03/1980</div></div>
      <div class="row data"><div>411</div><div>9</div><div>10</div><div>9999999999</div><div>Example</div><div>Examble H S</div><div>Alvorado</div><div>NATHALE</div><div>I</div><div>1234546734</div><div>F</div><div>28/03/1980</div></div>
    </div>
  </main>

  <nav class="pager">
    <div class="pages">Page : <b>1</b> <i>2 3 4.......25</i></div>
    <div class="btn next">Next</div>
    <div class="btn prev">Previous</div>
    <div class="show">Show</div>
    <div class="spinner"><span>10</span>
      <svg width="24" height="24" viewBox="0 0 24 24" aria-hidden="true">
        <path d="M2 10 L12 2 L22 10Z" fill="#3d5a60"/>
        <path d="M2 14 L12 22 L22 14Z" fill="#3d5a60"/>
      </svg>
    </div>
  </nav>
</body>
</html>
```